Valdane Companies Business Card Design

We need a new business card for our Private Equity Real Estate Development firm, “Valdane” and our EB-5 regional center “Thornmere Regional Center” on one card. We prefer a design that is simple, elegant, and represents the luxury products we design and build as well as the financial security and stability our successful history has produced. We are an industry leader in our field and 3rd generation family business that has evolved into an institutional quality investment platform. Considered design size is standard business card dimensions (3.5 x 2 inches with an additional 1/8 inch space for design elements or backgrounds that extend beyond the finished size of your piece.

Target Market(s)

• High net worth individuals
• Highly skilled technical workers and physicians in the US seeking investment-based immigration opportunities
• Sophisticated private equity investors
• Intermediary partners include domestic attorneys and investment brokers, as well as international agent networks
• US real estate developers

Industry/Entity Type

Finance

Contact Information for Business Card

(Providing placeholder info for personal information, please design for longer character spaces, longer names and addresses etc..)
• Logo for Valdane
• Logo for Thornmere Regional Center
• Full name: Marcus Valdane
• Job title: CEO
• Email address: mvaldane@valdanecompanies.com
• Cell phone number: +1.555.314.2287
• Office number +1.555.628.4410
• Office address: Larkfield Court 5, 4817 Vista Orilla, Marrowfield Valley.
• Website: www.valdanecompanies.com

Font styles to use
Serif
Sans Serif

Colors
ec1f27
ffffff
000000

Requirements
Must have
• • Logo for Valdane
• • Logo for Thornmere Regional Center
• - Use rounded corners
• (See .ai file included for logos)
Nice to have
• • Simple, elegant design
• • Aesthetically compatible with our website design (www.valdanecompanies.com)
• • Color palette including but not limited to white, black, and red (as per logos)
Should not have
• - Not too much red color
• - Do not stack both logos on top of each other

```html
<!DOCTYPE html>
<html lang="en">
<head>
<meta charset="utf-8">
<title>Valdane Companies Business Cards</title>
<link rel="stylesheet" href="https://fonts.googleapis.com/css2?family=Cinzel:wght@600;700&family=Crimson+Text:wght@400;600&family=Montserrat:wght@400&display=swap">
<style>
:root{
  --stage:#000000;
  --charcoal:#363636;
  --charcoal-bar:#3a3a3a;
  --crimson:#a31f30;
  --paper:#ffffff;
  --ink:#2a2a2a;
  --silver:#d4d4d4;
}
*{margin:0;padding:0;box-sizing:border-box}
html,body{width:1200px;height:1000px;overflow:hidden;background:var(--stage)}
.canvas{position:relative;width:1200px;height:1000px}
.card{position:absolute;overflow:hidden}
.card-front{width:525px;height:300px;left:62px;text-align:center}
.card-front.capital{top:178px;background:var(--charcoal)}
.card-front.center{top:516px;background:var(--crimson)}
.card-back{width:529px;height:304px;left:612px;background:var(--paper)}
.card-back.capital{top:174px}
.card-back.center{top:516px}

.front-mark{position:absolute;left:50%;top:60px;width:78px;height:78px;margin-left:-39px;background:var(--silver)}
.front-name{position:absolute;left:0;right:0;color:var(--paper);line-height:1}
.front-name .title{display:block;font-family:"Cinzel",serif;font-weight:700;font-size:48px;letter-spacing:0.5px}
.front-name .sub{display:block;font-family:"Montserrat",sans-serif;font-weight:400;font-size:14px;letter-spacing:6px;margin-top:8px;padding-left:6px}
.card-front.capital .front-name{top:170px}
.card-front.center .front-name{top:172px}

.back-logo{position:absolute;left:28px;top:29px;display:flex;align-items:center;gap:8px}
.back-logo .square{width:42px;height:42px}
.back-logo .divider{width:1px;height:42px}
.back-logo .words{line-height:1}
.back-logo .title{display:block;font-family:"Cinzel",serif;font-weight:700;font-size:28px}
.back-logo .sub{display:block;font-family:"Montserrat",sans-serif;font-size:9px;letter-spacing:3px;margin-top:3px;padding-left:2px}
.card-back.capital .back-logo{color:var(--charcoal)}
.card-back.capital .square,.card-back.capital .divider{background:var(--charcoal)}
.card-back.center .back-logo{color:var(--crimson)}
.card-back.center .square,.card-back.center .divider{background:var(--crimson)}

.person{position:absolute;right:27px;top:27px;text-align:right;font-family:"Crimson Text",serif;line-height:1.1}
.person .name{font-size:24px;font-weight:400;color:var(--ink)}
.person .role{font-size:15px;letter-spacing:1px;font-weight:400}
.card-back.capital .role{color:var(--ink)}
.card-back.center .role{color:var(--crimson)}
.edge-tab{position:absolute;right:0;top:28px;width:11px;height:44px}
.edge-bar{position:absolute;left:0;bottom:0;width:11px;height:150px}
.card-back.capital .edge-tab,.card-back.capital .edge-bar{background:var(--charcoal-bar)}
.card-back.center .edge-tab,.card-back.center .edge-bar{background:var(--crimson)}

.contact{position:absolute;left:28px;top:157px;list-style:none;font-family:"Crimson Text",serif;font-size:16.5px;letter-spacing:0.35px;color:var(--ink);line-height:18.6px}
.contact li{display:flex;align-items:center;gap:10px}
.contact svg{width:13px;height:13px;flex:none}
.address{position:absolute;left:28px;top:243px;font-family:"Crimson Text",serif;font-size:16.5px;letter-spacing:0.35px;color:var(--ink);line-height:18.6px}
.card-back.center .contact{top:158px}
.card-back.center .address{top:244px}
.card-back.capital .contact svg{fill:var(--ink)}
.card-back.center .contact svg{fill:var(--crimson)}
</style>
</head>
<body>
<main class="canvas">

  <section class="card card-front capital">
    <div class="front-mark"></div>
    <div class="front-name"><span class="title">VALDANE</span><span class="sub">CAPITAL</span></div>
  </section>

  <section class="card card-back capital">
    <div class="back-logo"><span class="square"></span><span class="divider"></span><span class="words"><span class="title">VALDANE</span><span class="sub">CAPITAL</span></span></div>
    <div class="person"><div class="name">Marcus Valdane</div><div class="role">CEO</div></div>
    <div class="edge-tab"></div>
    <ul class="contact">
      <li><svg viewBox="0 0 12 12"><path d="M3 0h6v12H3z M4 1v9h4V1z"/></svg>+1.555.314.2287</li>
      <li><svg viewBox="0 0 12 12"><path d="M0 4C2 1 10 1 12 4L10 5 9 4H3L2 5zM2 6h8v5H2z"/></svg>+1.555.628.4410</li>
      <li><svg viewBox="0 0 12 12"><path d="M0 2h12v8H0zM1 3l5 4 5-4z"/></svg>mvaldane@valdanecompanies.com</li>
      <li><svg viewBox="0 0 12 12"><path d="M6 0a6 6 0 1 0 0.01 0zM6 1.5a4.5 4.5 0 1 1-0.01 0zM5.4 1h1.2v10H5.4zM1 5.4h10v1.2H1z"/></svg>www.valdanecompanies.com</li>
    </ul>
    <p class="address">Larkfield Court 5, 4817 Vista Orilla<br>Marrowfield Valley</p>
    <div class="edge-bar"></div>
  </section>

  <section class="card card-front center">
    <div class="front-mark"></div>
    <div class="front-name"><span class="title">THORNMERE</span><span class="sub">REGIONAL CENTER</span></div>
  </section>

  <section class="card card-back center">
    <div class="back-logo"><span class="square"></span><span class="divider"></span><span class="words"><span class="title">THORNMERE</span><span class="sub">REGIONAL CENTER</span></span></div>
    <div class="person"><div class="name">Marcus Valdane</div><div class="role">CEO</div></div>
    <div class="edge-tab"></div>
    <ul class="contact">
      <li><svg viewBox="0 0 12 12"><path d="M3 0h6v12H3z M4 1v9h4V1z"/></svg>+1.555.314.2287</li>
      <li><svg viewBox="0 0 12 12"><path d="M0 4C2 1 10 1 12 4L10 5 9 4H3L2 5zM2 6h8v5H2z"/></svg>+1.555.628.4410</li>
      <li><svg viewBox="0 0 12 12"><path d="M0 2h12v8H0zM1 3l5 4 5-4z"/></svg>mvaldane@valdanecompanies.com</li>
      <li><svg viewBox="0 0 12 12"><path d="M6 0a6 6 0 1 0 0.01 0zM6 1.5a4.5 4.5 0 1 1-0.01 0zM5.4 1h1.2v10H5.4zM1 5.4h10v1.2H1z"/></svg>www.valdanecompanies.com</li>
    </ul>
    <p class="address">Larkfield Court 5, 4817 Vista Orilla<br>Marrowfield Valley</p>
    <div class="edge-bar"></div>
  </section>

</main>
</body>
</html>
```